Coastline Premier Retreats Business Card Design

Design a business card for Coastline Premier Retreats. Look at the website for colors and reference. Card should have logo, name, title, office number, mobile number, email, URL and a tagline like, "Luxury Hotel & Resort Email Marketing" (This might change).

https://www.coastlinepremierretreats.example

The rest I will leave up to your imagination.

Contact Information for Business Card

Logo, name, title, office number, mobile number, email, URL and a tagline like, "Luxury Hotel & Resort Email Marketing" (This might change).

```html
<!DOCTYPE html>
<html lang="en">
<head>
<meta charset="utf-8">
<title>Coastline Premier Retreats – Business Card</title>
<link href="https://fonts.googleapis.com/css2?family=Arimo:wght@400;700&display=swap" rel="stylesheet">
<style>
  :root {
    --bg: #cfd3d4;
    --paper: #f7f7f5;
    --orange: #e86c12;
    --ink: #3a3a3a;
    --muted: #555555;
    --white: #ffffff;
  }
  * { box-sizing: border-box; margin: 0; padding: 0; }
  html, body {
    width: 1200px; height: 829px; overflow: hidden;
    background: var(--bg);
    font-family: "Arimo", Arial, sans-serif;
  }
  .stage {
    position: relative; width: 1200px; height: 829px;
    display: flex; align-items: center; justify-content: center; gap: 50px;
  }
  .card {
    position: relative; width: 520px; height: 297px;
    box-shadow: 0 10px 28px rgba(0,0,0,.18);
  }
  .card--front { background: var(--paper); }
  .card--back { background: var(--orange); display: flex; align-items: center; justify-content: center; }

  .frame {
    position: absolute; inset: 18px;
    border: 1.5px solid var(--orange);
  }
  .wordmark {
    text-align: center; font-weight: 700; text-transform: uppercase;
    letter-spacing: .04em; line-height: 1.05;
  }
  .wordmark__main { display: block; }
  .wordmark__sub { display: block; letter-spacing: .28em; }

  .card--front .wordmark {
    position: absolute; top: 48px; left: 0; right: 0; color: #1e1e1e;
  }
  .card--front .wordmark__main { font-size: 30px; }
  .card--front .wordmark__sub { font-size: 11px; margin-top: 4px; }

  .card--back .wordmark { color: var(--white); }
  .card--back .wordmark__main { font-size: 52px; }
  .card--back .wordmark__sub { font-size: 18px; margin-top: 8px; }

  .person {
    position: absolute; top: 125px; right: 270px; text-align: right;
    font-size: 11px; color: var(--muted); line-height: 1.45;
  }
  .person__name {
    font-size: 21px; font-weight: 700; color: var(--orange);
    text-transform: uppercase; margin-bottom: 3px; white-space: nowrap;
  }
  .divider {
    position: absolute; left: 262px; top: 135px; width: 1px; height: 85px;
    background: var(--orange);
  }
  .contacts {
    position: absolute; left: 276px; top: 140px; list-style: none;
    font-size: 11px; color: var(--muted);
  }
  .contacts li { display: flex; align-items: center; gap: 7px; height: 19px; white-space: nowrap; }
  .contacts svg { width: 10px; height: 10px; flex: none; }
  .tagline {
    position: absolute; bottom: 11px; left: 0; right: 0; text-align: center;
  }
  .tagline span {
    background: var(--paper); padding: 0 12px;
    font-size: 12px; color: var(--ink);
  }
</style>
</head>
<body>
<main class="stage">
  <section class="card card--front" aria-label="Business card front">
    <div class="frame"></div>
    <div class="wordmark">
      <span class="wordmark__main">Coastline</span>
      <span class="wordmark__sub">Premier Retreats</span>
    </div>
    <div class="person">
      <p class="person__name">Daniel Hart</p>
      <p>CEO/Founder</p>
      <p>Po Box, 48 B Harbor St</p>
      <p>Shoreview, CA 90000</p>
    </div>
    <div class="divider"></div>
    <ul class="contacts">
      <li><svg viewBox="0 0 10 10"><rect x="2.5" y="0.5" width="5" height="9" rx="1" fill="none" stroke="#e86c12" stroke-width="1.2"/></svg>555.014.2290</li>
      <li><svg viewBox="0 0 10 10"><path d="M1 4 Q5 0 9 4 L8 5 L6.5 4 L6.5 3 Q5 2.5 3.5 3 L3.5 4 L2 5 Z" fill="#e86c12"/><rect x="2" y="5.5" width="6" height="3.5" rx=".6" fill="#e86c12"/></svg>+34 600 000 412</li>
      <li><svg viewBox="0 0 10 10"><rect x="0.5" y="2" width="9" height="6.5" fill="#e86c12"/><path d="M0.5 2 L5 5.5 L9.5 2" fill="none" stroke="#fff" stroke-width="1"/></svg>info@coastlinepremierretreats.example</li>
      <li><svg viewBox="0 0 10 10"><circle cx="5" cy="5" r="4.3" fill="none" stroke="#e86c12" stroke-width="1.2"/><path d="M0.7 5 H9.3 M5 0.7 Q2 5 5 9.3 M5 0.7 Q8 5 5 9.3" fill="none" stroke="#e86c12" stroke-width=".8"/></svg>www.coastlinepremierretreats.example</li>
    </ul>
    <p class="tagline"><span>Luxury Hotel &amp; Resort Email Marketing</span></p>
  </section>

  <section class="card card--back" aria-label="Business card back">
    <div class="wordmark">
      <span class="wordmark__main">Coastline</span>
      <span class="wordmark__sub">Premier Retreats</span>
    </div>
  </section>
</main>
</body>
</html>
```